I would like a business card to match my truck wrap and logo. I would like the font to match my existing business card please.

Industry/Entity Type

Painter

Contact Information for Business Card

Rodrigo Fenwar 801-437-2190 Fenwarcoatings.utah@brelmox.com
SERVICES - Custom Paint & Stain, Interior & Exterior, Epoxy Coatings / Garage Floors, Cabinet Refinishing, Log Staining and Refinishing.

Requirements
Nice to have
• I would like to have the white and grey line like the bottom of my vehicle wrap, Light Grey to match my truck also.

```html
<!DOCTYPE html>
<html lang="en">
<head>
<meta charset="utf-8">
<title>Fenwar Coatings — Business Card</title>
<link rel="stylesheet" href="https://fonts.googleapis.com/css2?family=Arimo:wght@400;700&display=swap">
<style>
  :root {
    --stage: #232221;
    --card: #ffffff;
    --brand-sky: #12aae8;
    --brand-deep: #0b7cc4;
    --brand-mark: #1488d0;
    --text-grey: #4a4a4a;
    --service-grey: #555555;
  }
  * { margin: 0; padding: 0; box-sizing: border-box; }
  html, body {
    width: 1065px;
    height: 1200px;
    overflow: hidden;
    background: var(--stage);
    font-family: "Arimo", Arial, sans-serif;
  }
  .stage { position: relative; width: 1065px; height: 1200px; }

  .card {
    position: absolute;
    width: 582px;
    height: 362px;
    background: var(--card);
    filter: drop-shadow(3px 3px 3px rgba(0,0,0,0.75));
  }
  .card--front {
    left: 292px; top: 218px;
    border-radius: 0 178px 178px 0 / 0 181px 181px 0;
  }
  .card--back {
    left: 263px; top: 623px;
    border-radius: 178px 0 0 178px / 181px 0 0 181px;
  }

  .brand {
    position: absolute;
    display: flex;
    align-items: center;
    gap: 22px;
  }
  .card--front .brand { left: 48px; top: 72px; }
  .card--back .brand { left: 100px; top: 59px; }
  .brand__square {
    width: 62px; height: 62px;
    background: var(--brand-mark);
  }
  .brand__name {
    color: var(--brand-sky);
    font-weight: 700;
    line-height: 1;
  }
  .brand__name-main {
    display: block;
    font-size: 45px;
    letter-spacing: 2px;
  }
  .brand__name-sub {
    display: block;
    margin-top: 8px;
    font-size: 15px;
    letter-spacing: 10.5px;
  }

  .person {
    position: absolute;
    left: 177px; top: 224px;
    color: var(--brand-deep);
    font-weight: 700;
    font-size: 23px;
    letter-spacing: 0.3px;
  }
  .contact {
    position: absolute;
    left: 178px; top: 274px;
    list-style: none;
    color: var(--text-grey);
    font-size: 17.5px;
  }
  .contact__item {
    display: flex;
    align-items: center;
    gap: 7px;
    height: 21.5px;
  }
  .contact__icon { width: 16px; height: 16px; flex: none; }

  .services {
    position: absolute;
    left: 224px; top: 165px;
    list-style: none;
    color: var(--service-grey);
    font-size: 18px;
  }
  .services__item {
    display: flex;
    align-items: center;
    gap: 9px;
    height: 28.8px;
  }
  .services__bullet {
    width: 12px; height: 12px;
    margin: 0 2px 0 2px;
    transform: rotate(45deg);
    background: linear-gradient(135deg, var(--brand-sky), var(--brand-deep));
    flex: none;
  }
</style>
</head>
<body>
<main class="stage">

  <section class="card card--front" aria-label="Card front">
    <div class="brand">
      <span class="brand__square"></span>
      <h1 class="brand__name">
        <span class="brand__name-main">FENWAR</span>
        <span class="brand__name-sub">COATINGS</span>
      </h1>
    </div>

    <p class="person">RODRIGO FENWAR</p>

    <ul class="contact">
      <li class="contact__item">
        <svg class="contact__icon" viewBox="0 0 24 24" aria-hidden="true">
          <path fill="#0b7cc4" d="M6.6 10.8c1.4 2.8 3.8 5.1 6.6 6.6l2.2-2.2c.3-.3.7-.4 1-.2 1.1.4 2.3.6 3.6.6.6 0 1 .4 1 1V20c0 .6-.4 1-1 1C10.6 21 3 13.4 3 4c0-.6.4-1 1-1h3.5c.6 0 1 .4 1 1 0 1.3.2 2.5.6 3.6.1.3 0 .7-.2 1L6.6 10.8z"/>
          <path fill="none" stroke="#0b7cc4" stroke-width="1.8" d="M14 2.5a8 8 0 0 1 7.5 7.5M14 6a4.5 4.5 0 0 1 4 4"/>
        </svg>
        <span>801-437-2190</span>
      </li>
      <li class="contact__item">
        <svg class="contact__icon" viewBox="0 0 24 24" aria-hidden="true">
          <rect x="1" y="5" width="22" height="14" fill="#0b7cc4"/>
          <path fill="none" stroke="#fff" stroke-width="1.6" d="M1 5l11 8 11-8M1 19l8-7M23 19l-8-7"/>
        </svg>
        <span>Fenwarcoatings.utah@brelmox.com</span>
      </li>
    </ul>
  </section>

  <section class="card card--back" aria-label="Card back">
    <div class="brand">
      <span class="brand__square"></span>
      <h2 class="brand__name">
        <span class="brand__name-main">FENWAR</span>
        <span class="brand__name-sub">COATINGS</span>
      </h2>
    </div>

    <ul class="services">
      <li class="services__item"><span class="services__bullet"></span>Custom Paint &amp; Stain</li>
      <li class="services__item"><span class="services__bullet"></span>Interior &amp; Exterior</li>
      <li class="services__item"><span class="services__bullet"></span>Epoxy Coatings/ Garage Floors</li>
      <li class="services__item"><span class="services__bullet"></span>Cabinet Refinishing</li>
      <li class="services__item"><span class="services__bullet"></span>Log Staining and Refinishing.</li>
    </ul>
  </section>

</main>
</body>
</html>
```